Business card for my new company (Accounting firm)

I need a business card for my new business Brightwell Advisory and Ledger SA. Our services are accounting, tax, audit and financial management. Our customers are small companies, start-ups and new companies. The final design has to show financial security, trust and growth. Please find our logo attached to the business card. Text for the business card: Brightwell Advisory and Ledger SA Tomas Varenholt Director and Founder Certified Accountant Tel. 022 418 57 34 tv@clairevalconseil.ch www.clairevalconseil.ch Rue des Vergières 27 1201 Geneva
Target Market(s)
Our customers are small companies, start-ups and new companies.
Industry/Entity Type
Finance And Accounting
Contact Information for Business Card
Claireval Conseil et Comptes SA
Tomas Varenholt
Directeur et Fondateur
Expert-comptable diplômé
Tél. 022 418 57 34
tv@clairevalconseil.ch
www.clairevalconseil.ch
Rue des Vergières 27
1201 Genève

```html
<!DOCTYPE html>
<html lang="fr">
<head>
<meta charset="utf-8">
<title>Claireval Conseil et Comptes SA – Carte de visite</title>
<link rel="stylesheet" href="https://fonts.googleapis.com/css2?family=Roboto:wght@400;500;700&display=swap">
<style>
  :root {
    --backdrop: #232122;
    --paper: #ffffff;
    --brand-navy: #1a6493;
    --brand-sky: #33ade0;
    --ink: #444444;
    --rule: #8a8a8a;
  }
  * { margin: 0; padding: 0; box-sizing: border-box; }
  html, body {
    width: 1125px; height: 1200px; overflow: hidden;
    background: var(--backdrop);
    font-family: "Roboto", Arial, sans-serif;
  }
  .canvas { position: relative; width: 1125px; height: 1200px; }
  .card {
    position: absolute; left: 171px; width: 826px; height: 472px;
  }
  .card--front { top: 106px; background: var(--paper); }
  .card--back { top: 639px; background: var(--brand-navy); }

  .brand-name {
    position: absolute; display: flex; align-items: center; gap: 14px;
    font-weight: 500; letter-spacing: 0.5px;
  }
  .card--front .brand-name {
    left: 60px; top: 210px; font-size: 40px; color: var(--brand-navy);
  }
  .brand-mark {
    width: 22px; height: 22px; border-radius: 50%; background: var(--brand-sky);
  }
  .card--back .brand-name {
    left: 0; right: 0; top: 195px; justify-content: center;
    font-size: 62px; color: var(--paper); letter-spacing: 3px;
  }
  .card--back .brand-mark { width: 30px; height: 30px; border-radius: 0; background: var(--paper); }

  .divider {
    position: absolute; left: 401px; top: 115px; width: 1.5px; height: 234px;
    background: var(--rule);
  }
  .contact { position: absolute; left: 434px; top: 110px; color: var(--ink); }
  .contact__name {
    font-size: 30px; font-weight: 700; color: var(--brand-sky); line-height: 34px;
  }
  .contact__role { font-size: 20px; line-height: 27px; }
  .contact__address { margin-top: 16px; font-size: 19px; line-height: 25px; }
  .contact__list { margin-top: 14px; list-style: none; font-size: 19px; line-height: 26px; }
  .contact__list li { display: flex; align-items: center; gap: 9px; }
  .contact__list svg { width: 18px; height: 18px; fill: var(--brand-sky); flex: none; }
</style>
</head>
<body>
<main class="canvas">
  <section class="card card--front">
    <div class="brand-name"><span class="brand-mark"></span>Claireval</div>
    <div class="divider"></div>
    <div class="contact">
      <p class="contact__name">Tomas Varenholt</p>
      <p class="contact__role">Directeur et Fondateur</p>
      <p class="contact__role">Expert-comptable diplômé</p>
      <p class="contact__address">Rue des Vergières 27<br>1201 Genève</p>
      <ul class="contact__list">
        <li><svg viewBox="0 0 24 24"><path d="M6.6 10.8a15.1 15.1 0 0 0 6.6 6.6l2.2-2.2c.3-.3.7-.4 1-.2 1.1.4 2.3.6 3.6.6.6 0 1 .4 1 1V20c0 .6-.4 1-1 1A17 17 0 0 1 3 4c0-.6.4-1 1-1h3.5c.6 0 1 .4 1 1 0 1.3.2 2.5.6 3.6.1.3 0 .7-.2 1z"/></svg>022 418 57 34</li>
        <li><svg viewBox="0 0 24 24"><path d="M2 5h20v14H2z M3.5 6.5 12 13l8.5-6.5" fill="none" stroke="#33ade0" stroke-width="2"/></svg>tv@clairevalconseil.ch</li>
        <li><svg viewBox="0 0 24 24"><circle cx="12" cy="12" r="10"/><path d="M2 12h20M12 2c3 3 3 17 0 20M12 2c-3 3-3 17 0 20" fill="none" stroke="#fff" stroke-width="1.3"/></svg>www.clairevalconseil.ch</li>
      </ul>
    </div>
  </section>

  <section class="card card--back">
    <div class="brand-name"><span class="brand-mark"></span>CLAIREVAL</div>
  </section>
</main>
</body>
</html>
```